Business Card Design Project

We are a construction company in Orange County, CA. We need a two sided business card. We would like the back to be our logo with web URL. Front should included Name, title, address, phone, fax and email address.

our address is
627 West Dorrance Blvd, Suite 308
Anaheim, CA 92718

Our logo files are attached.

Construction

```html
<!DOCTYPE html>
<html lang="en">
<head>
<meta charset="utf-8">
<title>Corvane Business Card</title>
<link href="https://fonts.googleapis.com/css2?family=Source+Sans+3:wght@400;600;700;800&display=swap" rel="stylesheet">
<style>
  :root {
    --brand-blue: #164a7c;
    --ink: #3a3a3a;
    --muted: #555555;
    --card: #ffffff;
    --stage: #ececec;
    --rule: #1f2a36;
  }
  * { margin: 0; padding: 0; box-sizing: border-box; }
  html, body { width: 1200px; height: 405px; overflow: hidden; }
  body {
    background: var(--stage);
    font-family: "Source Sans 3", "Helvetica Neue", Arial, sans-serif;
    position: relative;
  }
  .card {
    position: absolute;
    top: 47px;
    width: 525px;
    height: 300px;
    background: var(--card);
    box-shadow: 0 1px 3px rgba(0,0,0,.18);
  }
  .card-front { left: 50px; }
  .card-back { left: 607px; }

  .wordmark {
    position: absolute;
    left: 0; right: 0;
    text-align: center;
    color: var(--brand-blue);
    font-weight: 800;
    line-height: 1;
    letter-spacing: -1px;
  }
  .card-front .wordmark { top: 30px; font-size: 70px; }
  .card-back .wordmark { top: 88px; font-size: 70px; }

  .name-band {
    position: absolute;
    left: 0; right: 0;
    top: 136px;
    height: 40px;
    border-top: 2px solid var(--rule);
    border-bottom: 2px solid var(--rule);
    padding: 3px 0;
  }
  .name-band-fill {
    height: 100%;
    background: var(--brand-blue);
    color: #fff;
    text-align: center;
    font-size: 20px;
    line-height: 30px;
  }
  .person-name { font-weight: 700; }
  .person-title { font-weight: 400; }

  .address {
    position: absolute;
    right: 278px;
    top: 214px;
    text-align: right;
    font-size: 14px;
    line-height: 17px;
    color: var(--ink);
  }
  .divider {
    position: absolute;
    left: 265px;
    top: 206px;
    width: 1px;
    height: 72px;
    background: #9a9a9a;
  }
  .contacts {
    position: absolute;
    left: 285px;
    top: 204px;
    list-style: none;
    font-size: 14px;
    line-height: 17px;
    color: var(--ink);
  }
  .contacts li { display: flex; align-items: center; gap: 6px; }
  .contacts svg { width: 10px; height: 10px; fill: var(--ink); flex: none; }

  .web-url {
    position: absolute;
    left: 0; right: 0;
    top: 192px;
    text-align: center;
    font-size: 15px;
    letter-spacing: 2.5px;
    color: var(--muted);
  }
</style>
</head>
<body>
  <section class="card card-front">
    <div class="wordmark">CORVANE</div>
    <div class="name-band">
      <div class="name-band-fill"><span class="person-name">Your Name,</span> <span class="person-title">Title</span></div>
    </div>
    <address class="address" style="font-style:normal">
      627 West Dorrance Blvd<br>
      Suite 308, Anaheim<br>
      CA&nbsp; 92718
    </address>
    <div class="divider"></div>
    <ul class="contacts">
      <li>
        <svg viewBox="0 0 10 10" aria-hidden="true"><path d="M2 .5 3.6 2.6 2.7 3.6c.6 1.4 1.8 2.6 3.2 3.2l1-.9L9 7.5 8 9.5C4.2 9.2.8 5.8.5 2z"/></svg>
        01-555-0148
      </li>
      <li>
        <svg viewBox="0 0 10 10" aria-hidden="true"><path d="M2.5 1h5v2.5h-5zM.5 4h9v4.5h-9zM2.5 6h5v3h-5z"/></svg>
        01-555-0149
      </li>
      <li>
        <svg viewBox="0 0 10 10" aria-hidden="true"><path d="M.5 2h9v6h-9zM1 2.4 5 5.6 9 2.4" stroke="#fff" stroke-width=".8"/></svg>
        info@corvane.com
      </li>
      <li>
        <svg viewBox="0 0 10 10" aria-hidden="true"><circle cx="5" cy="5" r="4.5"/><path d="M.5 5h9M5 .5c-2.4 2.6-2.4 6.4 0 9M5 .5c2.4 2.6 2.4 6.4 0 9" stroke="#fff" stroke-width=".7" fill="none"/></svg>
        www.corvane.com
      </li>
    </ul>
  </section>

  <section class="card card-back">
    <div class="wordmark">CORVANE</div>
    <div class="web-url">www.corvane.com</div>
  </section>
</body>
</html>
```